VL - menu design

Hi,

We require elegant menu design for upscale restaurant. Please find attached the logo and the menu items for your reference.

for inspiration, this is a good website: -
http://www.plateworthy-sample.net/dishcraft/about.php

We are very much open for Menu Size suggestions.

unfortunately the place is going under renovation, we don't have updated images to it. the closest look and feel to our place is http://vazelo-example.com ..

we are also open for creative options on the shape, the styles, etc. as long as it represents the fine dine feel ...

Thanks ...

Dear All,

We wouldlike to extend our apology for not being able to provide feedbacks on everysingle design. We were extremely busy and we have multiple contests opensimultaneously which makes the process even harder.

However,we would like to thank you all for the efforts you have put into designingour menu. It is very much appreciated …

We wishyou all success in your design ventures and we are quite positive that we willbe working with many of you on many projects in the soon future. 

Thanks & Regards,

DQI Team...

 

 

 

Industry/Entity Type

Restaurant

Requirements
Must have
• Please ensure that there are 'some' images in the menu ... this is very important.
Should not have
• IMPORTANT: -

1. Please DO NOT insert any currency sign to the menu
2. Please keep the prices of the menu at the end of the menu items descriptions NOT beside the menu item names. The font of the price should be similar to the menu item description and please DO NOT bold the numbers. the prices should be subtle.

Thank you ...

```html
<!DOCTYPE html>
<html lang="en">
<head>
<meta charset="utf-8">
<title>Vela Lane Café – Menu</title>
<link href="https://fonts.googleapis.com/css2?family=Crimson+Text:ital,wght@0,400;0,700;1,400;1,700&family=Dosis:wght@300;500&display=swap" rel="stylesheet">
<style>
  :root {
    --paper: #ffffff;
    --ink: #1e1e1e;
    --rule: #b9b9b9;
    --heading: #555555;
    --taupe: #9a8470;
    --sketch-light: #efebe4;
    --sketch-dark: #cfc6b8;
  }
  html, body {
    margin: 0;
    padding: 0;
    width: 1200px;
    height: 1200px;
    overflow: hidden;
    background: var(--paper);
  }
  .menu {
    position: relative;
    width: 1200px;
    height: 1200px;
    color: var(--ink);
    font-family: "Crimson Text", Georgia, serif;
  }

  /* Brand */
  .brand {
    position: absolute;
    left: 97px;
    top: 78px;
    display: flex;
    align-items: center;
    gap: 18px;
    font-family: "Dosis", sans-serif;
    font-weight: 500;
    color: var(--ink);
  }
  .brand-square {
    width: 26px;
    height: 26px;
    background: var(--ink);
  }
  .brand-name {
    font-size: 46px;
    letter-spacing: 8px;
    line-height: 1;
  }
  .brand-name small {
    display: block;
    font-size: 18px;
    letter-spacing: 12px;
    margin-top: 10px;
    text-align: right;
  }

  /* Artwork placeholders */
  .pizza-art {
    position: absolute;
    left: 683px;
    top: 88px;
    width: 250px;
    height: 165px;
    border-radius: 50%;
    background: radial-gradient(ellipse at 50% 45%, var(--sketch-light) 0%, var(--sketch-dark) 100%);
  }
  .cherry-art {
    position: absolute;
    left: 75px;
    top: 825px;
    width: 92px;
    height: 108px;
    border-radius: 40% 40% 45% 45%;
    background: linear-gradient(160deg, var(--sketch-light), var(--sketch-dark));
  }

  /* Headings */
  .section-title {
    font-family: "Dosis", sans-serif;
    font-weight: 300;
    font-size: 36px;
    letter-spacing: 2px;
    color: var(--heading);
    margin: 0;
    text-align: center;
    line-height: 1;
  }

  /* Pizza column */
  .pizza-frame {
    position: absolute;
    left: 555px;
    top: 242px;
    width: 545px;
    height: 833px;
    border-top: 1px solid var(--rule);
    border-left: 1px solid var(--rule);
  }
  .pizza {
    position: absolute;
    left: 555px;
    top: 250px;
    width: 550px;
    text-align: center;
  }
  .pizza .section-title { margin-bottom: 20px; }
  .pizza-item { margin-bottom: 15px; }
  .pizza-name {
    font-weight: 700;
    font-size: 21px;
    line-height: 26px;
    color: var(--taupe);
  }
  .pizza-desc {
    font-style: italic;
    font-size: 15.5px;
    line-height: 18px;
  }

  /* Specialties */
  .specialties {
    position: absolute;
    left: 100px;
    top: 325px;
    width: 397px;
    height: 450px;
  }
  .specialties-frame {
    position: absolute;
    inset: 0;
  }
  .specialties-body {
    position: absolute;
    left: 40px;
    right: 40px;
    top: 40px;
    text-align: center;
  }
  .specialties .section-title { margin-bottom: 22px; }
  .dish { margin-bottom: 16px; font-style: italic; font-size: 15.5px; line-height: 20px; }
  .dish-name { font-weight: 700; }

  /* Desserts */
  .desserts-rule {
    position: absolute;
    left: 158px;
    top: 828px;
    width: 325px;
    border-top: 1px solid var(--rule);
  }
  .desserts {
    position: absolute;
    left: 158px;
    top: 838px;
    width: 300px;
    text-align: center;
    font-style: italic;
    font-size: 15.5px;
    line-height: 20px;
  }
  .desserts .section-title { margin-bottom: 20px; }
  .sweet { margin-bottom: 14px; }
  .sweet-name { font-weight: 700; }
</style>
</head>
<body>
<main class="menu">

  <header class="brand">
    <span class="brand-square"></span>
    <div class="brand-name">VELA LANE<small>CAFÉ</small></div>
  </header>

  <div class="pizza-art" role="img" aria-label="Hand-drawn sketch of a whole pizza"></div>

  <div class="pizza-frame"></div>
  <section class="pizza">
    <h2 class="section-title">THE PIZZA</h2>
    <div class="pizza-item"><div class="pizza-name">Margherita</div><div class="pizza-desc">Fresh cherry tomato, Buffalo Mozzarella, fresh basil. 69</div></div>
    <div class="pizza-item"><div class="pizza-name">Marinara</div><div class="pizza-desc">Tomato, salted Anchovies, fresh garlic, capers, oregano. 59</div></div>
    <div class="pizza-item"><div class="pizza-name">Capricciosa</div><div class="pizza-desc">Tomato, Buffalo Mozzarella, mushrooms, black olives,<br>Artichokes, Turkey ham. 79</div></div>
    <div class="pizza-item"><div class="pizza-name">Tonno e cipolle</div><div class="pizza-desc">Tomato, olive oil tuna, red onions, black olives. 79</div></div>
    <div class="pizza-item"><div class="pizza-name">Frutti di mare</div><div class="pizza-desc">Fresh cherry tomatoes, Mussels, Prawns, Calamari,<br>Mozzarella, Olives. 99</div></div>
    <div class="pizza-item"><div class="pizza-name">Prosciutto e funghi</div><div class="pizza-desc">Tomato, Turkey ham, Porcini mushrooms, Parmesan slices. 89</div></div>
    <div class="pizza-item"><div class="pizza-name">Calzone</div><div class="pizza-desc">Tomato, Ricotta cheese, Mozzarella, Turkey ham,<br>Porcini mushrooms, Chicken Sausages. 79</div></div>
    <div class="pizza-item"><div class="pizza-name">Quattro formaggi</div><div class="pizza-desc">Mozzarella, Gorgonzola cheese, Fontina cheese, Parmesan slices.</div></div>
    <div class="pizza-item"><div class="pizza-name">Vegetariana</div><div class="pizza-desc">Fresh cherry tomatoes, Mozzarella, Zucchini, Aubergines,<br>Bell Peppers, Escarole, Red onions. 69</div></div>
    <div class="pizza-item"><div class="pizza-name">Vela Lane</div><div class="pizza-desc">Fresh cherry tomatoes, Buffalo Mozzarella,<br>Asparagus tops, “Richelieu” style Beef Sirloin,<br>fresh Porcini mushrooms, Truffle oil. 159</div></div>
    <div class="pizza-item"><div class="pizza-name">Camel</div><div class="pizza-desc">Special pizza with camel Meat flavored in<br>Emirates style topped with mozzarella cheese. 89</div></div>
  </section>

  <section class="specialties">
    <svg class="specialties-frame" width="397" height="450" viewBox="0 0 397 450" aria-hidden="true">
      <g fill="none" stroke="#b9b9b9" stroke-width="1">
        <rect x="14" y="14" width="369" height="422"/>
        <rect x="22" y="22" width="353" height="406"/>
        <polyline points="0,22 14,6 383,6 397,22"/>
        <polyline points="0,428 14,444 383,444 397,428"/>
        <line x1="0" y1="22" x2="0" y2="428"/>
        <line x1="397" y1="22" x2="397" y2="428"/>
      </g>
    </svg>
    <div class="specialties-body">
      <h2 class="section-title">OUR SPECIALTIES</h2>
      <div class="dish"><span class="dish-name">Astice e Tartufo Pizza</span><br>Fresh cherry tomatoes, Lobster medallions,<br>Asparagus tops, Mozzarella, fresh Truffle. 459</div>
      <div class="dish"><span class="dish-name">Beef Tenderloin “ALLA Rossini”</span> with<br>Foie Gras and white Truffle, gratin potatoes and<br>black peppered vegetables. 489</div>
      <div class="dish"><span class="dish-name">Traditional italian T-bone steak</span><br>“ALLA Florentina” (minimum 1 Kg) with<br>grilled vegetables, Porcini mushrooms, Bernaise<br>sauce and baked potatoes. 589</div>
      <div class="dish"><span class="dish-name">Fettuccine with fresh white Truffle</span><br>on a leek and chives sauce. 299</div>
    </div>
  </section>

  <div class="cherry-art" role="img" aria-label="Hand-drawn sketch of a pair of cherries"></div>
  <div class="desserts-rule"></div>
  <section class="desserts">
    <h2 class="section-title">DESSERTS</h2>
    <div class="sweet"><span class="sweet-name">Amaretto Tiramisù.</span> 40</div>
    <div class="sweet"><span class="sweet-name">Meringata</span><br>Traditional Italian meringue with vanilla cream,<br>fresh strawberry and dark chocolate curls. 60</div>
    <div class="sweet"><span class="sweet-name">Fresh Fruit Tart</span></div>
    <div class="sweet"><span class="sweet-name">A slice of cake</span></div>
    <div class="sweet"><span class="sweet-name">Choice of our home made cakes</span></div>
  </section>

</main>
</body>
</html>
```